UI Improvement for FlorKeep app

We are looking for a talented UI/UX designer to REFINE and enhance the visual design of our mobile application, FlorKeep. The app is fully functional, but we need a designer to improve its aesthetics by specifying design elements such as fonts, colors, spacing, and component styles.
Your task will be to analyze the CURRENT UI and provide detailed design specifications that will make the app more visually appealing, modern, and user-friendly.
TODO:
Review the existing FlorKeep app design (see attachments) and identify areas for visual improvement.
Provide a detailed UI style guide, including:
Typography (font choices, sizes, and weights)
Color palette (primary, secondary, and accent colors)
Component styling (buttons, forms, icons, and interactive elements)
Spacing and layout guidelines (margins, paddings, and alignment)
Ensure the design remains clean, modern, and professional while maintaining usability and accessibility.
Provide design mockups or visual examples (if possible) to illustrate the proposed changes.
Deliverables:
A UI Style Guide (PDF or Figma file) with specifications on fonts, colors, spacing, and UI components.
Optionally, before/after mockups or examples demonstrating the improvements.
Ideal Designer:
Strong experience in mobile UI/UX design.
Understanding of modern design trends and best practices.
Ability to communicate design choices clearly for easy developer implementation.
I have attached 7 images showcasing the main UI screens used in the FlorKeep app. These screens need visual enhancements to improve their overall look and user experience.
The images represent the current design in three key modes:
LIST Mode – Displays data in a structured list format.
READ Mode – Shows detailed information when a user selects an item.
ADD/EDIT Mode – Allows users to input or modify information.
Additionally, there is a ‘MORE’ page, which serves as a menu listing other features of the application.
Task Objective:
Please refine and improve these UIs to create a more modern, visually appealing, and user-friendly experience. Focus on typography, colors, spacing, and component styling to ensure a cohesive and polished design.
Look and feel
Each slider illustrates characteristics of the customer's brand and the style your logo design should communicate.

```html
<!DOCTYPE html>
<html lang="en">
<head>
<meta charset="utf-8">
<title>FlorKeep – Contact, Pilot and More screens</title>
<link href="https://fonts.googleapis.com/css2?family=Poppins:wght@400;500;600;700&display=swap" rel="stylesheet">
<style>
:root{
  --canvas:#e6e6e6;
  --blue:#1f5fae;
  --ink:#1c1c1c;
  --muted:#555;
  --line:#cfd6df;
  --row:#eef2f7;
  --pale-yellow:#fdfbd9;
  --pale-cyan:#e0fdfd;
  --green:#90e98c;
  --white:#fff;
}
*{box-sizing:border-box;margin:0;padding:0}
html,body{width:1200px;height:771px;overflow:hidden;background:var(--canvas);font-family:"Poppins",sans-serif;color:var(--ink)}
.screen{position:absolute;top:52px;width:331px;height:658px;background:var(--white);overflow:hidden}
.screen--contact{left:60px}
.screen--pilot{left:439px;background:linear-gradient(160deg,#1d5db0 0%,#2a74cc 35%,#1a56a6 65%,#2668bd 100%)}
.screen--more{left:818px}
.topbar{position:absolute;left:0;top:0;width:100%;height:60px;background:linear-gradient(180deg,#2466b7,#1c58a6);border-radius:0 0 18px 18px}
.screen--pilot .topbar{background:none;height:48px;border-bottom:1px solid rgba(255,255,255,.25);left:16px;width:299px;border-radius:0}
.topbar__title{position:absolute;left:0;right:0;top:18px;text-align:center;color:var(--white);font-weight:700;font-size:16px;letter-spacing:.3px}
.screen--pilot .topbar__title{top:10px}
.round-btn{position:absolute;top:16px;width:24px;height:24px;border-radius:50%;background:rgba(255,255,255,.18);display:flex;align-items:center;justify-content:center}
.round-btn--back{left:16px}.round-btn--menu{right:16px}
.screen--pilot .round-btn{top:9px}
.screen--pilot .round-btn--back{left:0}.screen--pilot .round-btn--menu{right:0}

.add-row{position:absolute;left:15px;width:300px;height:34px;border:1px solid var(--line);border-radius:3px;display:flex;align-items:center;justify-content:space-between;padding:0 5px 0 11px;font-size:10px;font-weight:500}
.plus{width:26px;height:24px;background:var(--blue);border-radius:3px;color:#fff;font-size:15px;font-weight:600;display:flex;align-items:center;justify-content:center}
.card{position:absolute;left:16px;width:300px;border-radius:4px;padding:14px 14px 0 15px;box-shadow:0 1px 4px rgba(0,0,0,.08)}
.card--pilots{top:257px;height:77px;background:var(--pale-yellow)}
.card--owner{top:342px;height:111px;background:var(--pale-cyan)}
.card--qualified{top:463px;height:110px;background:var(--green)}
.card__head{display:flex;align-items:center;gap:8px}
.card__icon{width:26px;height:26px;border-radius:4px;background:#8a8f94}
.card__title{font-size:11px;font-weight:700;flex:1}
.card__toggle{font-size:8px;color:#444}
.card__body{margin-top:9px;font-size:9.3px;line-height:15px;display:flex;justify-content:space-between;gap:10px}
.chev{flex:none;margin-top:3px}
.card__add{margin-top:6px;font-size:7px;color:#444;display:flex;align-items:center;gap:6px}
.card__add span{width:10px;height:10px;border:1px solid #444;border-radius:50%;display:inline-flex;align-items:center;justify-content:center;font-size:8px;line-height:1}

.detail{position:absolute;left:16px;top:68px;width:299px;height:253px;background:var(--white);border-radius:7px;padding:14px 13px;display:flex;flex-direction:column;gap:9px}
.detail__row{height:38px;background:var(--row);border-radius:2px;padding:6px 9px;position:relative}
.detail__label{font-size:8.8px;font-weight:500}
.detail__value{font-size:7.5px;color:var(--muted);margin-top:2px}
.detail__dots{position:absolute;right:14px;top:10px;font-weight:700;font-size:12px;letter-spacing:1px}
.accordion{position:absolute;left:16px;width:299px;color:#fff;font-size:7.5px;font-weight:500;display:flex;justify-content:space-between;align-items:center;padding-bottom:12px;border-bottom:1px solid rgba(255,255,255,.35)}
.contact-info{position:absolute;top:528px;display:flex;align-items:center;gap:9px;color:#fff;line-height:15px}
.contact-info__dot{width:24px;height:24px;border-radius:50%;background:#fff;display:flex;align-items:center;justify-content:center}
.contact-info b{display:block;font-size:10.5px;font-weight:600}
.contact-info small{display:block;font-size:9.5px;font-weight:500}

.menu-row{position:absolute;left:15px;width:297px;height:35px;background:var(--row);border:1px solid var(--line);border-radius:2px;display:flex;align-items:center;justify-content:space-between;padding:0 9px 0 14px;font-size:11px;font-weight:600}
.menu-icon{width:25px;height:25px;background:var(--blue);border-radius:3px;display:flex;align-items:center;justify-content:center}

.tabbar{position:absolute;left:0;top:592px;width:100%;height:66px;background:linear-gradient(180deg,#2466b7,#1b55a2);border-radius:18px 18px 0 0;display:flex;justify-content:space-around;padding:0 10px}
.tab{width:60px;display:flex;flex-direction:column;align-items:center;padding-top:14px;color:#fff;font-size:8.5px;font-weight:600}
.tab__icon{width:24px;height:24px;border-radius:50%;display:flex;align-items:center;justify-content:center;margin-bottom:7px}
.tab--active .tab__icon{background:#fff}
</style>
</head>
<body>

<section class="screen screen--contact">
  <header class="topbar">
    <span class="round-btn round-btn--back"><svg width="10" height="10" viewBox="0 0 10 10"><path d="M9 5H1M4 2L1 5l3 3" stroke="#fff" stroke-width="1.3" fill="none"/></svg></span>
    <h1 class="topbar__title">CONTACT</h1>
    <span class="round-btn round-btn--menu"><svg width="11" height="9" viewBox="0 0 11 9"><path d="M1 1h9M3 4.5h7M1 8h9" stroke="#fff" stroke-width="1.2"/></svg></span>
  </header>

  <div class="add-row" style="top:75px">Add Personal Information -e<span class="plus">+</span></div>
  <div class="add-row" style="top:120px">Add Work Info -e<span class="plus">+</span></div>
  <div class="add-row" style="top:165px">Add Skills/Talents -e<span class="plus">+</span></div>
  <div class="add-row" style="top:210px">Add Resources -e<span class="plus">+</span></div>

  <article class="card card--pilots">
    <div class="card__head"><span class="card__icon" role="img" aria-label="Pilot figure icon"></span><span class="card__title">PILOTS -E</span><span class="card__toggle">Collapse</span></div>
    <div class="card__body"><span>Hollis, Dean, 4719305, 10/31/23</span><svg class="chev" width="8" height="5" viewBox="0 0 8 5"><path d="M1 1l3 3 3-3" stroke="#333" stroke-width="1.2" fill="none"/></svg></div>
  </article>
  <article class="card card--owner">
    <div class="card__head"><span class="card__icon" role="img" aria-label="Pilot figure icon"></span><span class="card__title">AIRCRAFT OWNER -E</span><span class="card__toggle">Collapse</span></div>
    <div class="card__body"><span>Personal: Hollis, Dean: Corvane: K4R: C<br>orvane Aircraft Company, Single Engine, 1100</span><svg class="chev" width="8" height="5" viewBox="0 0 8 5"><path d="M1 1l3 3 3-3" stroke="#333" stroke-width="1.2" fill="none"/></svg></div>
    <div class="card__add"><span>+</span>Add Aircraft Owner-e</div>
  </article>
  <article class="card card--qualified">
    <div class="card__head"><span class="card__icon" role="img" aria-label="Pilot figure icon"></span><span class="card__title">QUALIFIED PILOT-E</span><span class="card__toggle">Collapse</span></div>
    <div class="card__body"><span>Hollis, Dean: Corvane: K4R: Corvane Aircraft<br>Company, Single Engine, 1100</span><svg class="chev" width="8" height="5" viewBox="0 0 8 5"><path d="M1 1l3 3 3-3" stroke="#333" stroke-width="1.2" fill="none"/></svg></div>
    <div class="card__add"><span>+</span>Add Qualified Pilot -e</div>
  </article>

  <nav class="tabbar">
    <div class="tab tab--active"><span class="tab__icon"><svg width="14" height="14" viewBox="0 0 14 14"><path d="M3 2l2 3-1 1c1 2 2 3 4 4l1-1 3 2-1 2C6 13 1 8 1 3z" fill="#1f5fae"/></svg></span>Contact</div>
    <div class="tab"><span class="tab__icon"><svg width="14" height="14" viewBox="0 0 14 14"><circle cx="7" cy="4" r="3" fill="#fff"/><path d="M1 13c0-4 3-5 6-5s6 1 6 5z" fill="#fff"/></svg></span>Pilot</div>
    <div class="tab"><span class="tab__icon"><svg width="14" height="14" viewBox="0 0 14 14"><path d="M12 1L1 6l5 1 1 5 5-11z" fill="#fff"/></svg></span>Plane</div>
    <div class="tab"><span class="tab__icon"><svg width="14" height="14" viewBox="0 0 14 14"><circle cx="6" cy="4" r="3" fill="#fff"/><path d="M0 13c0-4 3-5 6-5 1 0 2 0 3 1v4z" fill="#fff"/><circle cx="11" cy="11" r="2.5" fill="#fff"/></svg></span>Flt Request</div>
    <div class="tab"><span class="tab__icon"><svg width="4" height="14" viewBox="0 0 4 14"><circle cx="2" cy="2" r="1.4" fill="#fff"/><circle cx="2" cy="7" r="1.4" fill="#fff"/><circle cx="2" cy="12" r="1.4" fill="#fff"/></svg></span>More</div>
  </nav>
</section>

<section class="screen screen--pilot" role="img" aria-label="Pilot detail screen over a blue marbled background">
  <header class="topbar">
    <span class="round-btn round-btn--back"><svg width="10" height="10" viewBox="0 0 10 10"><path d="M9 5H1M4 2L1 5l3 3" stroke="#fff" stroke-width="1.3" fill="none"/></svg></span>
    <h1 class="topbar__title">PILOT</h1>
    <span class="round-btn round-btn--menu"><svg width="11" height="9" viewBox="0 0 11 9"><path d="M1 1h9M3 4.5h7M1 8h9" stroke="#fff" stroke-width="1.2"/></svg></span>
  </header>

  <div class="detail">
    <div class="detail__row"><div class="detail__label">PILOT-E</div><div class="detail__value">Marsh, Owen, Trent</div><span class="detail__dots">···</span></div>
    <div class="detail__row"><div class="detail__label">PILOT CERTIFICATE NO-E</div><div class="detail__value">5206418</div></div>
    <div class="detail__row"><div class="detail__label">MEDICAL EXPIRATION DATE -E</div><div class="detail__value">9/30/24</div></div>
    <div class="detail__row"><div class="detail__label">FLIGHT REVIEW EXPIRATION DATE -E</div><div class="detail__value">6/30/24</div></div>
    <div class="detail__row"><div class="detail__label">TOTAL FLIGHT TIME-E</div><div class="detail__value">2500</div></div>
  </div>

  <div class="accordion" style="top:349px"><span>X91, Pine Hollow Airport, Pine Hollow, FL, 32600, 11, 2500</span><svg width="8" height="5" viewBox="0 0 8 5"><path d="M1 1l3 3 3-3" stroke="#fff" stroke-width="1.2" fill="none"/></svg></div>
  <div class="accordion" style="top:392px"><span>C92, Ridgeview Municipal Airport, Ridgeview, CO, 80399, 5,334 ft, 4,800 ft</span><svg width="8" height="5" viewBox="0 0 8 5"><path d="M1 1l3 3 3-3" stroke="#fff" stroke-width="1.2" fill="none"/></svg></div>
  <div class="accordion" style="top:435px"><span>Add Base Airport-e</span><svg width="8" height="5" viewBox="0 0 8 5"><path d="M1 1l3 3 3-3" stroke="#fff" stroke-width="1.2" fill="none"/></svg></div>
  <div class="accordion" style="top:477px"><span>Add Ratings -e</span><svg width="8" height="5" viewBox="0 0 8 5"><path d="M1 1l3 3 3-3" stroke="#fff" stroke-width="1.2" fill="none"/></svg></div>

  <div class="contact-info" style="left:50px"><span class="contact-info__dot"><svg width="11" height="11" viewBox="0 0 14 14"><circle cx="7" cy="4" r="3" fill="#1f5fae"/><path d="M1 13c0-4 3-5 6-5s6 1 6 5z" fill="#1f5fae"/></svg></span><div><b>Contact -e</b><small>Nora Vance</small></div></div>
  <div class="contact-info" style="left:179px"><span class="contact-info__dot"><svg width="11" height="11" viewBox="0 0 14 14"><path d="M3 1l2 3-1 1.5c1 2 2.5 3.5 4.5 4.5L10 9l3 2-1 2.5C6 13 1 8 .8 2z" fill="#1f5fae"/></svg></span><div><b>Phone -e</b><small>555-014-2290</small></div></div>

  <nav class="tabbar">
    <div class="tab"><span class="tab__icon"><svg width="14" height="14" viewBox="0 0 14 14"><path d="M3 2l2 3-1 1c1 2 2 3 4 4l1-1 3 2-1 2C6 13 1 8 1 3z" fill="#fff"/></svg></span>Contact</div>
    <div class="tab tab--active"><span class="tab__icon"><svg width="14" height="14" viewBox="0 0 14 14"><circle cx="7" cy="4" r="3" fill="#1f5fae"/><path d="M1 13c0-4 3-5 6-5s6 1 6 5z" fill="#1f5fae"/></svg></span>Pilot</div>
    <div class="tab"><span class="tab__icon"><svg width="14" height="14" viewBox="0 0 14 14"><path d="M12 1L1 6l5 1 1 5 5-11z" fill="#fff"/></svg></span>Plane</div>
    <div class="tab"><span class="tab__icon"><svg width="14" height="14" viewBox="0 0 14 14"><circle cx="6" cy="4" r="3" fill="#fff"/><path d="M0 13c0-4 3-5 6-5 1 0 2 0 3 1v4z" fill="#fff"/><circle cx="11" cy="11" r="2.5" fill="#fff"/></svg></span>Flt Request</div>
    <div class="tab"><span class="tab__icon"><svg width="4" height="14" viewBox="0 0 4 14"><circle cx="2" cy="2" r="1.4" fill="#fff"/><circle cx="2" cy="7" r="1.4" fill="#fff"/><circle cx="2" cy="12" r="1.4" fill="#fff"/></svg></span>More</div>
  </nav>
</section>

<section class="screen screen--more">
  <header class="topbar">
    <span class="round-btn round-btn--back"><svg width="10" height="10" viewBox="0 0 10 10"><path d="M9 5H1M4 2L1 5l3 3" stroke="#fff" stroke-width="1.3" fill="none"/></svg></span>
    <h1 class="topbar__title">MORE</h1>
    <span class="round-btn round-btn--menu"><svg width="11" height="9" viewBox="0 0 11 9"><path d="M1 1h9M3 4.5h7M1 8h9" stroke="#fff" stroke-width="1.2"/></svg></span>
  </header>

  <div class="menu-row" style="top:78px">FLIGHT<span class="menu-icon"><svg width="13" height="13" viewBox="0 0 14 14"><path d="M12 1L1 6l5 1 1 5 5-11z" fill="#fff"/></svg></span></div>
  <div class="menu-row" style="top:121px">LOGIN<span class="menu-icon"><svg width="12" height="12" viewBox="0 0 14 14"><circle cx="7" cy="4" r="3" fill="#fff"/><path d="M1 13c0-4 3-5 6-5s6 1 6 5z" fill="#fff"/></svg></span></div>
  <div class="menu-row" style="top:165px">ACCOUNT<span class="menu-icon"><svg width="13" height="12" viewBox="0 0 15 14"><circle cx="6" cy="4" r="3" fill="#fff"/><path d="M0 13c0-4 3-5 6-5 1 0 2 0 3 1v4z" fill="#fff"/><circle cx="12" cy="10" r="2.2" fill="none" stroke="#fff" stroke-width="1.4"/></svg></span></div>
  <div class="menu-row" style="top:207px">CALENDAR<span class="menu-icon"><svg width="12" height="12" viewBox="0 0 12 12"><rect x="1" y="2" width="10" height="9" fill="none" stroke="#fff" stroke-width="1.3"/><path d="M1 4.5h10M3.5 7h1M6 7h1M8.5 7h1M3.5 9h1M6 9h1" stroke="#fff"/></svg></span></div>
  <div class="menu-row" style="top:250px">USERS<span class="menu-icon"><svg width="14" height="12" viewBox="0 0 16 12"><circle cx="8" cy="3" r="2.3" fill="#fff"/><circle cx="3" cy="4" r="1.7" fill="#fff"/><circle cx="13" cy="4" r="1.7" fill="#fff"/><path d="M4 12c0-4 2-5 4-5s4 1 4 5zM0 12c0-3 1-4 3-4v4zM16 12c0-3-1-4-3-4v4z" fill="#fff"/></svg></span></div>
  <div class="menu-row" style="top:293px">DASHBOARD<span class="menu-icon"><svg width="12" height="12" viewBox="0 0 12 12"><rect x="0" y="0" width="5" height="7" fill="#fff"/><rect x="7" y="0" width="5" height="4" fill="#fff"/><rect x="0" y="8" width="5" height="4" fill="#fff"/><rect x="7" y="5" width="5" height="7" fill="#fff"/></svg></span></div>
  <div class="menu-row" style="top:337px">TRACKING<span class="menu-icon"><svg width="12" height="14" viewBox="0 0 12 14"><path d="M6 0a4 4 0 014 4c0 3-4 7-4 7S2 7 2 4a4 4 0 014-4z" fill="#fff"/><circle cx="6" cy="4" r="1.5" fill="#1f5fae"/><path d="M0 13h12" stroke="#fff" stroke-width="1.3"/></svg></span></div>
  <div class="menu-row" style="top:379px">OUTREACH EVENT<span class="menu-icon"><svg width="13" height="13" viewBox="0 0 14 14"><circle cx="7" cy="3" r="2" fill="#fff"/><circle cx="3" cy="7" r="1.6" fill="#fff"/><circle cx="11" cy="7" r="1.6" fill="#fff"/><path d="M4 14c0-4 1.5-5 3-5s3 1 3 5z" fill="#fff"/></svg></span></div>
  <div class="menu-row" style="top:422px">MAINTENANCE RESOURCE<span class="menu-icon"><svg width="4" height="13" viewBox="0 0 4 13"><rect x="1" y="0" width="2" height="13" fill="#fff"/></svg></span></div>
  <div class="menu-row" style="top:465px">SETTING<span class="menu-icon"><svg width="13" height="13" viewBox="0 0 14 14"><circle cx="7" cy="7" r="4.5" fill="none" stroke="#fff" stroke-width="3" stroke-dasharray="2.2 1.3"/><circle cx="7" cy="7" r="3.2" fill="none" stroke="#fff" stroke-width="1.6"/></svg></span></div>

  <nav class="tabbar">
    <div class="tab"><span class="tab__icon"><svg width="14" height="14" viewBox="0 0 14 14"><path d="M3 2l2 3-1 1c1 2 2 3 4 4l1-1 3 2-1 2C6 13 1 8 1 3z" fill="#fff"/></svg></span>Contact</div>
    <div class="tab"><span class="tab__icon"><svg width="14" height="14" viewBox="0 0 14 14"><circle cx="7" cy="4" r="3" fill="#fff"/><path d="M1 13c0-4 3-5 6-5s6 1 6 5z" fill="#fff"/></svg></span>Pilot</div>
    <div class="tab"><span class="tab__icon"><svg width="14" height="14" viewBox="0 0 14 14"><path d="M12 1L1 6l5 1 1 5 5-11z" fill="#fff"/></svg></span>Plane</div>
    <div class="tab"><span class="tab__icon"><svg width="14" height="14" viewBox="0 0 14 14"><circle cx="6" cy="4" r="3" fill="#fff"/><path d="M0 13c0-4 3-5 6-5 1 0 2 0 3 1v4z" fill="#fff"/><circle cx="11" cy="11" r="2.5" fill="#fff"/></svg></span>Flt Request</div>
    <div class="tab tab--active"><span class="tab__icon"><svg width="4" height="14" viewBox="0 0 4 14"><circle cx="2" cy="2" r="1.4" fill="#1f5fae"/><circle cx="2" cy="7" r="1.4" fill="#1f5fae"/><circle cx="2" cy="12" r="1.4" fill="#1f5fae"/></svg></span>More</div>
  </nav>
</section>

</body>
</html>
```